Business Card Design For A Renovation Contractor Company

We need a business card for a new company based in Singapore, our company name is "RB Tolvane". We are a renovation contractor that builds designs into reality. We build more of F&B restaurants, retail stores and commercial offices. We work very closely with designers. The final design should communicate to our client that we are a company that you can trust, that will plan and complete your project without giving you a headache. I like my client to remember my company as "RB". The beauty of SIMPLE is important.

Industry/Entity Type

Contractor

Requirements
Nice to have
• Black or Red base

```html
<!DOCTYPE html>
<html lang="en">
<head>
<meta charset="utf-8">
<title>RB Tolvane — Business Card</title>
<link rel="stylesheet" href="https://fonts.googleapis.com/css2?family=Open+Sans:wght@300;400;600;700&display=swap">
<style>
  :root {
    --bg: #e9e6e1;
    --card-white: #ffffff;
    --card-black: #050505;
    --brand-red: #e31b23;
    --ink: #1a1a1a;
    --ink-soft: #4a4a4a;
    --rule: #b9b9b9;
    --paper-shadow: rgba(0,0,0,0.22);
  }
  * { box-sizing: border-box; margin: 0; padding: 0; }
  html, body { width: 1200px; height: 720px; overflow: hidden; }
  body {
    background: var(--bg);
    font-family: "Open Sans", Arial, sans-serif;
    color: var(--ink);
    position: relative;
  }
  .card {
    position: absolute;
    top: 205px;
    width: 540px;
    height: 309px;
    box-shadow: 0 10px 26px var(--paper-shadow);
    overflow: hidden;
  }
  .card-front { left: 40px; background: var(--card-white); }
  .card-back  { left: 620px; background: var(--card-black); }

  .card-shapes { position: absolute; inset: 0; }

  .holder {
    position: absolute;
    right: 22px;
    top: 12px;
    text-align: right;
    color: var(--card-white);
  }
  .holder-name { font-size: 17px; font-weight: 700; line-height: 1.1; }
  .holder-title { font-size: 11px; font-weight: 400; }

  .brand {
    position: absolute;
    left: 36px;
    top: 98px;
    width: 270px;
  }
  .brand-row { display: flex; align-items: center; gap: 12px; }
  .brand-dot {
    width: 34px; height: 34px;
    border-radius: 50%;
    background: var(--brand-red);
    flex: none;
  }
  .brand-name {
    font-size: 38px;
    font-weight: 300;
    letter-spacing: -0.5px;
    line-height: 1;
    color: var(--ink);
  }
  .brand-tagline {
    margin-top: 6px;
    padding-top: 3px;
    border-top: 1px solid var(--rule);
    font-size: 14px;
    font-weight: 400;
    letter-spacing: 0.4px;
    color: var(--ink);
  }

  .contact {
    position: absolute;
    left: 36px;
    top: 212px;
    list-style: none;
    font-size: 12.5px;
    line-height: 18px;
    color: var(--ink-soft);
  }
  .contact li { display: flex; align-items: center; gap: 8px; }
  .contact svg { width: 11px; height: 11px; flex: none; }

  .address {
    position: absolute;
    left: 240px;
    top: 212px;
    padding-left: 12px;
    border-left: 1px solid var(--rule);
    height: 52px;
    font-size: 12.5px;
    font-style: normal;
    line-height: 18px;
    color: var(--ink-soft);
  }

  .back-brand {
    position: absolute;
    left: 0; right: 0;
    top: 108px;
    display: flex;
    justify-content: center;
    align-items: center;
    gap: 14px;
  }
  .back-dot {
    width: 40px; height: 40px;
    border-radius: 50%;
    background: var(--card-white);
  }
  .back-name {
    font-size: 48px;
    font-weight: 300;
    color: var(--card-white);
    letter-spacing: -0.5px;
  }
  .back-web {
    position: absolute;
    left: 0; right: 0;
    bottom: 52px;
    text-align: center;
    font-size: 15px;
    letter-spacing: 4px;
    color: var(--card-white);
  }
</style>
</head>
<body>

  <section class="card card-front" aria-label="Business card front">
    <svg class="card-shapes" viewBox="0 0 540 309" aria-hidden="true">
      <path class="corner-red" d="M205 0 H540 V46 L205 84 Z" fill="var(--brand-red)"/>
      <path class="corner-black" d="M205 84 L540 46 V62 C498 66 486 104 506 142 Z" fill="var(--card-black)"/>
    </svg>

    <div class="holder">
      <div class="holder-name">Your Name</div>
      <div class="holder-title">Title</div>
    </div>

    <div class="brand">
      <div class="brand-row">
        <span class="brand-dot"></span>
        <span class="brand-name">RB Tolvane</span>
      </div>
      <div class="brand-tagline">spaces built as designed</div>
    </div>

    <ul class="contact">
      <li>
        <svg viewBox="0 0 12 12"><circle cx="6" cy="6" r="6" fill="var(--brand-red)"/><path d="M4 3.2 L5 3 5.6 4.6 5 5.1 C5.3 5.9 6 6.6 6.9 7 L7.4 6.4 9 7 8.8 8 C6 8.4 3.6 6 4 3.2Z" fill="#fff"/></svg>
        123-456-0789
      </li>
      <li>
        <svg viewBox="0 0 12 12"><circle cx="6" cy="6" r="6" fill="var(--brand-red)"/><rect x="4.3" y="2.8" width="3.4" height="6.4" rx="0.6" fill="#fff"/><rect x="4.9" y="3.6" width="2.2" height="4" fill="var(--brand-red)"/></svg>
        123-456-0789
      </li>
      <li>
        <svg viewBox="0 0 12 12"><circle cx="6" cy="6" r="6" fill="var(--brand-red)"/><rect x="3" y="4" width="6" height="4.2" fill="#fff"/><path d="M3 4 L6 6.4 9 4" fill="none" stroke="var(--brand-red)" stroke-width="0.7"/></svg>
        info@rbtolvane.com
      </li>
      <li>
        <svg viewBox="0 0 12 12"><circle cx="6" cy="6" r="6" fill="var(--brand-red)"/><circle cx="6" cy="6" r="3" fill="none" stroke="#fff" stroke-width="0.8"/><path d="M3 6 H9 M6 3 V9" stroke="#fff" stroke-width="0.6"/></svg>
        www.rbtolvane.com
      </li>
    </ul>

    <address class="address">
      Street Name, City Name<br>
      State Zip Code
    </address>
  </section>

  <section class="card card-back" aria-label="Business card back">
    <div class="back-brand">
      <span class="back-dot"></span>
      <span class="back-name">RB Tolvane</span>
    </div>
    <div class="back-web">www.rbtolvane.com</div>
  </section>

</body>
</html>
```